Thornbury Building Company - Card Design

I am looking to use the logo designs that you already did for me to develop a business card. I would like the card to have a black background and be double sided. I want white and green logo and text. I have attached an inspiration photo of a look that I like. I would like to use the Vertical Logo attached to take up the full front side of the card. On the back where I have my name and information, I would like to have the horizontal logo or maybe even just the image of the 'A' and trees without the text. I am open, but I am looking for something clean and simple and I want the green to really pop! Additional files can be found under Design #: 58302946

Target Market(s)

Homeowners

Industry/Entity Type

Construction

Contact Information for Business Card

Name: Marcus Thornbury, Title: Project Manager, Phone: 555.274.8136, Email: thornburybuildingcompany@mailvesta.com, address: 487 Larkspur Ln, Felton, CA 95033, Lic# 2468317

Colors
00AB8E
00BBA5
67D7C9
C6EFE9
E9F9F6

Requirements
Nice to have
• I would like to see the logos that I have already got from ArtLoomHub, though I am open to new ones

```html
<!DOCTYPE html>
<html lang="en">
<head>
<meta charset="utf-8">
<title>Thornbury Building Company – Business Card</title>
<link rel="stylesheet" href="https://fonts.googleapis.com/css2?family=Arimo:wght@400;700&display=swap">
<style>
  :root {
    --backdrop: #b9b9b9;
    --card: #1c1c1c;
    --green: #5cc23d;
    --white: #ffffff;
    --muted: #e6e6e6;
  }
  * { margin: 0; padding: 0; box-sizing: border-box; }
  html, body {
    width: 1200px; height: 788px; overflow: hidden;
    background: var(--backdrop);
    font-family: "Arimo", Arial, sans-serif;
  }
  .sheet {
    position: relative; width: 1200px; height: 788px;
    display: flex; align-items: center; justify-content: center; gap: 40px;
  }
  .card {
    position: relative; width: 540px; height: 309px;
    background: var(--card); border-radius: 22px;
    box-shadow: 0 14px 30px rgba(0,0,0,.28);
    color: var(--white); overflow: hidden;
  }
  .wordmark { display: flex; align-items: center; gap: 12px; }
  .wordmark-square { flex: none; background: var(--green); }
  .wordmark-name {
    font-weight: 700; color: var(--white); text-transform: uppercase;
    letter-spacing: .04em; line-height: 1.15;
  }

  /* contact side */
  .card-contact .wordmark { position: absolute; left: 34px; top: 168px; width: 200px; }
  .card-contact .wordmark-square { width: 30px; height: 30px; }
  .card-contact .wordmark-name { font-size: 15px; }
  .divider {
    position: absolute; left: 248px; top: 70px; width: 1px; height: 170px;
    background: var(--green);
  }
  .details { position: absolute; left: 268px; top: 64px; width: 250px; }
  .person-name { font-size: 21px; font-weight: 700; color: var(--green); text-transform: uppercase; letter-spacing: .01em; }
  .person-title { font-size: 12px; color: var(--muted); margin-top: 3px; }
  .licence { font-size: 12px; color: var(--green); margin-top: 16px; }
  .address { font-size: 12px; color: var(--muted); margin-top: 3px; }
  .contact-line { display: flex; align-items: center; gap: 6px; font-size: 11.5px; color: var(--muted); margin-top: 12px; }
  .contact-line + .contact-line { margin-top: 5px; }
  .contact-line svg { width: 11px; height: 11px; flex: none; fill: var(--green); }

  /* logo side */
  .card-logo { display: flex; align-items: center; justify-content: center; }
  .card-logo .wordmark { gap: 18px; }
  .card-logo .wordmark-square { width: 56px; height: 56px; }
  .card-logo .wordmark-name { font-size: 27px; }
</style>
</head>
<body>
<main class="sheet">
  <section class="card card-contact" aria-label="Business card, contact side">
    <div class="wordmark">
      <span class="wordmark-square"></span>
      <span class="wordmark-name">Thornbury Building Company</span>
    </div>
    <div class="divider"></div>
    <div class="details">
      <p class="person-name">Marcus Thornbury</p>
      <p class="person-title">Project Manager</p>
      <p class="licence">Lic# 2468317</p>
      <p class="address">487 Larkspur Ln, Felton, CA 95033</p>
      <p class="contact-line">
        <svg viewBox="0 0 24 24" aria-hidden="true"><path d="M6.6 10.8a15.1 15.1 0 0 0 6.6 6.6l2.2-2.2a1 1 0 0 1 1-.25 11.4 11.4 0 0 0 3.6.57 1 1 0 0 1 1 1V20a1 1 0 0 1-1 1A17 17 0 0 1 3 4a1 1 0 0 1 1-1h3.5a1 1 0 0 1 1 1c0 1.25.2 2.45.57 3.6a1 1 0 0 1-.25 1z"/></svg>
        555.274.8136
      </p>
      <p class="contact-line">
        <svg viewBox="0 0 24 24" aria-hidden="true"><path d="M2 5h20v14H2z M2 5l10 8 10-8" stroke="#1c1c1c" stroke-width="1.5"/></svg>
        thornburybuildingcompany@mailvesta.com
      </p>
    </div>
  </section>

  <section class="card card-logo" aria-label="Business card, logo side">
    <div class="wordmark">
      <span class="wordmark-square"></span>
      <span class="wordmark-name">Thornbury<br>Building Company</span>
    </div>
  </section>
</main>
</body>
</html>
```